FunBrixo Business Card

We need a business card design for our company. We sell construction-themed amusement rides for kids.

Contact Information for Business Card

Contact info on business card should include:
Carl Dunning
Co-Founder & COO
(833) 571-FUNBRIX
Carl@funbrixo-demo.com
www.funbrixo-demo.com

```html
<!DOCTYPE html>
<html lang="en">
<head>
<meta charset="UTF-8">
<title>FunBrixo Business Card</title>
<link href="https://fonts.googleapis.com/css2?family=Poppins:wght@400;500;700&display=swap" rel="stylesheet">
<style>
  :root {
    --backdrop: #e4e4e6;
    --card: #1c1c1e;
    --edge: #f07f22;
    --orange: #f5832a;
    --blue: #29a9e0;
    --white: #e9e9ea;
    --divider: #5a3a24;
  }
  * { margin: 0; padding: 0; box-sizing: border-box; }
  html, body { width: 1200px; height: 801px; overflow: hidden; }
  body {
    background: var(--backdrop);
    font-family: "Poppins", sans-serif;
    display: flex;
    align-items: center;
    justify-content: center;
    gap: 40px;
  }
  .card {
    width: 530px;
    height: 303px;
    background: var(--card);
    border-bottom: 2px solid var(--edge);
    border-left: 2px solid var(--edge);
    box-shadow: 0 10px 24px rgba(0,0,0,0.25);
    position: relative;
    display: flex;
    align-items: center;
  }
  .brand {
    display: flex;
    align-items: center;
    gap: 10px;
    color: var(--orange);
    font-weight: 700;
  }
  .brand-dot {
    width: 14px; height: 14px;
    border-radius: 50%;
    background: var(--orange);
  }
  /* contact side */
  .card-contact .brand { font-size: 30px; width: 250px; justify-content: center; }
  .card-contact .divider {
    width: 1px; height: 82px;
    background: var(--divider);
    margin-top: -20px;
  }
  .details { padding-left: 22px; margin-top: -20px; }
  .name {
    color: var(--orange);
    font-weight: 700;
    font-size: 15px;
    text-transform: uppercase;
    line-height: 1.2;
  }
  .role { color: var(--blue); font-size: 12px; font-weight: 500; margin-bottom: 8px; }
  .contact-line {
    display: flex; align-items: center; gap: 8px;
    color: var(--white);
    font-size: 11px;
    line-height: 1.55;
  }
  .contact-line svg { width: 10px; height: 10px; fill: var(--orange); flex: none; }
  /* logo side */
  .card-logo { justify-content: center; }
  .card-logo .brand { font-size: 52px; gap: 14px; }
  .card-logo .brand-dot { width: 22px; height: 22px; }
</style>
</head>
<body>
  <section class="card card-contact">
    <div class="brand"><span class="brand-dot"></span>FunBrixo</div>
    <div class="divider"></div>
    <div class="details">
      <p class="name">Carl Dunning</p>
      <p class="role">Co-Founder &amp; COO</p>
      <p class="contact-line">
        <svg viewBox="0 0 10 10"><path d="M2 0.5 L3.6 2.8 L2.7 3.8 Q3.8 6.2 6.2 7.3 L7.2 6.4 L9.5 8 L8.4 9.5 Q3 9 0.5 1.6 Z"/></svg>
        (833) 571-FUNBRIX
      </p>
      <p class="contact-line">
        <svg viewBox="0 0 10 10"><path d="M0 2 H10 V8.5 H0 Z M0.6 2.4 L5 5.6 L9.4 2.4 V3.2 L5 6.4 L0.6 3.2 Z" fill-rule="evenodd"/></svg>
        Carl@funbrixo-demo.com
      </p>
      <p class="contact-line">
        <svg viewBox="0 0 10 10"><circle cx="5" cy="5" r="4.6"/><path d="M0.6 5 H9.4 M5 0.6 Q2.5 5 5 9.4 M5 0.6 Q7.5 5 5 9.4" stroke="#1c1c1e" stroke-width="0.8" fill="none"/></svg>
        www.funbrixo-demo.com
      </p>
    </div>
  </section>

  <section class="card card-logo">
    <div class="brand"><span class="brand-dot"></span>FunBrixo</div>
  </section>
</body>
</html>
```